Need Help having my business card stand out

I am the owner of Birchway Canine Training and would like for my business cards to stand out. I have been trying to keep designing them myself but I can't get what I have in my head on the card. I will try my best to post templates that I like for inspirations. I want something unique but elegant. I don't want in to look cartoony or cheesy. It needs to pop in a pet shop but also in a coffee shop or gym.

Target Market(s)

Dog owners, Married ,No young kids Jr High school kids and up (maybe kids on the way) Executives, Stay at home moms/wives, Small business owners

Industry/Entity Type

Dog Training

Contact Information for Business Card

Lowell Spratt, 281-904-3376, info@birchwaycanine.example, www.birchwaycanine.example

Colors

Designer to choose colors to be used in the design.

Requirements
Must have
• my logo
Should not have
• Cursive lettering

```html
<!DOCTYPE html>
<html lang="en">
<head>
<meta charset="utf-8">
<title>Birchway Canine Training — Business Card</title>
<link rel="stylesheet" href="https://fonts.googleapis.com/css2?family=Open+Sans:wght@400;600;700&display=swap">
<style>
  :root {
    --backdrop: #a8a8a8;
    --card-white: #ffffff;
    --card-black: #000000;
    --ink: #111111;
    --paper-text: #ffffff;
  }
  * { margin: 0; padding: 0; box-sizing: border-box; }
  html, body {
    width: 1200px;
    height: 900px;
    overflow: hidden;
  }
  body {
    background: var(--backdrop);
    font-family: "Open Sans", Arial, sans-serif;
    position: relative;
  }
  .card {
    position: absolute;
    top: 307px;
    width: 440px;
    height: 271px;
    border-radius: 12px;
    overflow: hidden;
  }
  .card--front { left: 149px; background: var(--card-white); }
  .card--back  { left: 609px; background: var(--card-black); }

  .brand-lockup {
    position: absolute;
    left: 0;
    right: 0;
    display: flex;
    flex-direction: column;
    align-items: center;
  }
  .brand-mark {
    border-radius: 50%;
    flex: none;
  }
  .brand-name {
    text-align: center;
    font-weight: 700;
    text-transform: uppercase;
    letter-spacing: 0.05em;
    line-height: 1.15;
  }
  .card--front .brand-lockup { top: 24px; }
  .card--front .brand-mark {
    width: 50px;
    height: 50px;
    background: var(--ink);
    margin-bottom: 10px;
  }
  .card--front .brand-name {
    font-size: 21px;
    color: var(--ink);
  }
  .card--back .brand-lockup { top: 58px; }
  .card--back .brand-mark {
    width: 62px;
    height: 62px;
    background: var(--paper-text);
    margin-bottom: 12px;
  }
  .card--back .brand-name {
    font-size: 25px;
    color: var(--paper-text);
  }

  .holder-name {
    position: absolute;
    top: 164px;
    left: 0;
    right: 0;
    text-align: center;
    font-size: 15px;
    font-weight: 600;
    color: var(--ink);
    letter-spacing: 0.01em;
  }
  .contact-band {
    position: absolute;
    left: 0;
    right: 0;
    bottom: 0;
    height: 62px;
    padding: 0 22px;
    background: var(--card-black);
    color: var(--paper-text);
    display: flex;
    align-items: center;
    justify-content: center;
    font-size: 9.5px;
    white-space: nowrap;
  }
  .contact-band .label { font-weight: 700; }
  .contact-band .sep { margin: 0 5px; }
</style>
</head>
<body>
  <section class="card card--front" aria-label="Business card front">
    <div class="brand-lockup">
      <span class="brand-mark" aria-hidden="true"></span>
      <div class="brand-name">Birchway Canine<br>Training</div>
    </div>
    <div class="holder-name">LOWELL SPRATT</div>
    <div class="contact-band">
      <span><span class="label">P:</span> 281-904-3376</span>
      <span class="sep">|</span>
      <span><span class="label">E:</span> info@birchwaycanine.example</span>
      <span class="sep">|</span>
      <span>www.birchwaycanine.example</span>
    </div>
  </section>

  <section class="card card--back" aria-label="Business card back">
    <div class="brand-lockup">
      <span class="brand-mark" aria-hidden="true"></span>
      <div class="brand-name">Birchway Canine<br>Training</div>
    </div>
  </section>
</body>
</html>
```